MEDICAL CLINIC LETTERHEAD

Design is a letterhead for a non-profit medical center. The name of the clinic is VITARIDGE Community Health Center. Although the full name must be included, the community health center part is more of a description and should be less visible - i attached an example of what I mean by that (ATTACHED IMAGE IS AN EXAMPLE OF FONT SIZES NOT A DESIGN IDEA). Please design something modern, cool looking and unique because I can always download free templates.
Phone, email, website and etc will be added later.

Industry/Entity Type

MEDICAL

```html
<!DOCTYPE html>
<html lang="en">
<head>
<meta charset="utf-8">
<title>VITARIDGE Community Health Center – Letterhead</title>
<link href="https://fonts.googleapis.com/css2?family=Questrial&family=Open+Sans:wght@600&display=swap" rel="stylesheet">
<style>
  :root{
    --paper:#ffffff;
    --ink-name:#4a4a4a;
    --ink-heading:#9b9b9b;
    --ink-body:#8c8c8c;
    --ink-date:#8a8a8a;
    --accent-blue:#27aae1;
    --accent-orange:#fbad42;
    --signature-tone:#ececec;
  }
  *{box-sizing:border-box;margin:0;padding:0}
  html,body{width:908px;height:1200px;overflow:hidden;background:var(--paper)}
  body{font-family:"Questrial",sans-serif;color:var(--ink-body)}
  .letterhead{position:relative;width:908px;height:1200px;background:var(--paper)}

  .brand{position:absolute;left:32px;top:82px;display:flex;flex-direction:column}
  .brand-mark{display:flex;align-items:center;gap:8px}
  .brand-dot{width:14px;height:14px;border-radius:50%;background:var(--accent-orange)}
  .brand-name{font-size:27px;letter-spacing:.5px;color:var(--ink-name);line-height:1}
  .brand-descriptor{font-size:10.5px;letter-spacing:.3px;color:var(--ink-name);margin-top:4px;margin-left:22px}

  .sender{position:absolute;left:41px;top:290px}
  .sender-name{font-size:28px;color:var(--ink-heading);letter-spacing:.5px;margin-bottom:10px}
  .sender-line{font-size:15.5px;line-height:28px;color:var(--ink-body)}
  .sender-address{font-size:15.5px;line-height:20px;margin-top:2px}

  .letter-date{position:absolute;right:43px;top:440px;font-family:"Open Sans",sans-serif;font-weight:600;font-size:17px;color:var(--ink-date)}

  .letter-body{position:absolute;left:36px;width:829px;font-size:16.3px;line-height:19.6px;text-align:justify;color:var(--ink-body)}
  .body-first{top:461px}
  .body-second{top:599px}
  .body-third{top:737px}

  .sign-off{position:absolute;left:577px;top:872px}
  .sign-off-title{font-size:23px;color:var(--ink-body)}
  .signature{width:168px;height:100px;margin-top:22px;margin-left:19px;background:var(--signature-tone);border-radius:4px}

  .contact-band{position:absolute;left:223px;top:1142px;right:0;height:46px}
  .band-cap{position:absolute;left:0;top:0;width:46px;height:46px;border-radius:50%;background:var(--accent-blue)}
  .band-bar{position:absolute;left:23px;right:0;top:9px;height:29px;background:var(--accent-blue);display:flex;align-items:center;justify-content:flex-end;padding-right:43px;gap:14px;color:#fff;font-size:16px}
  .contact-item{display:flex;align-items:center;gap:4px;white-space:nowrap}
  .contact-item svg{width:13px;height:13px}
</style>
</head>
<body>
<main class="letterhead">
  <header class="brand">
    <div class="brand-mark">
      <span class="brand-dot"></span>
      <span class="brand-name">VITARIDGE</span>
    </div>
    <span class="brand-descriptor">COMMUNITY HEALTH CENTER</span>
  </header>

  <section class="sender">
    <h1 class="sender-name">DANA MORROW</h1>
    <p class="sender-line">0198-765-432</p>
    <p class="sender-line">hello@northlakeoffice.com</p>
    <p class="sender-address">4821 Harbor View Ln. Suite<br>210 Denver, CO 80202</p>
  </section>

  <p class="letter-date">12 December, 2023</p>

  <p class="letter-body body-first">Lorem ipsum dolor sit amet, consectetuer adipiscing elit, sed diam nonummy nibh euismod tincidunt ut laoreet dolore magna aliquam erat volutpat. Ut wisi enim ad minim veniam, quis nostrud exerci tation ullamcorper suscipit lobortis nisl ut aliquip ex ea commodo consequat. Duis autem vel eum iriure dolor in hendrerit in vulputate velit esse molestie consequat, vel illum dolore eu feugiat nulla facilisis at vero eros et accumsan et iusto odio dignissim qui blandit praesent luptatum zzril delenit augue duis dolore te feugait nulla facilisi.</p>

  <p class="letter-body body-second">Lorem ipsum dolor sit amet, cons ectetuer adipiscing elit, sed diam nonummy nibh euismod tincidunt ut laoreet dolore magna aliquam erat volutpat. Ut wisi enim ad minim veniam, quis nostrud exerci tation ullamcorper suscipit lobortis nisl ut aliquip ex ea commodo consequat.<br>Lorem ipsum dolor sit amet, consectetuer adipiscing elit, sed diam nonummy nibh euismod tincidunt ut laoreet dolore magna aliquam erat</p>

  <p class="letter-body body-third">Lorem ipsum dolor sit amet, cons ectetuer adipiscing elit, sed diam nonummy nibh euismod tincidunt ut laoreet dolore magna aliquam erat volutpat. Ut wisi enim ad minim veniam, quis nostrud exerci tation ullamcorper suscipit lobortis nisl ut aliquip ex ea commodo consequat. Lorem ipsum dolor sit zamet, consectetuer adipiscing elit, sed diam nonummy nibh euismod tincidunt.</p>

  <section class="sign-off">
    <p class="sign-off-title">Managing Director</p>
    <div class="signature" role="img" aria-label="Handwritten signature of the managing director"></div>
  </section>

  <footer class="contact-band">
    <span class="band-cap"></span>
    <div class="band-bar">
      <span class="contact-item">
        <svg viewBox="0 0 16 16" aria-hidden="true"><circle cx="8" cy="8" r="8" fill="#fff"/><path d="M5.2 4.2l1.4-.3.8 2-1 .8a6 6 0 0 0 2.9 2.9l.8-1 2 .8-.3 1.4c-3.5.2-6.8-3.1-6.6-6.6z" fill="var(--accent-blue)"/></svg>
        0198-765-432
      </span>
      <span class="contact-item">
        <svg viewBox="0 0 16 16" aria-hidden="true"><circle cx="8" cy="8" r="8" fill="#fff"/><rect x="4" y="5" width="8" height="6" rx="1" fill="none" stroke="var(--accent-blue)" stroke-width="1.2"/><path d="M4.3 5.5L8 8.5l3.7-3" fill="none" stroke="var(--accent-blue)" stroke-width="1.2"/></svg>
        info@vitaridge.org
      </span>
      <span class="contact-item">
        <svg viewBox="0 0 16 16" aria-hidden="true"><circle cx="8" cy="8" r="7" fill="none" stroke="#fff" stroke-width="1.3"/><ellipse cx="8" cy="8" rx="3" ry="7" fill="none" stroke="#fff" stroke-width="1.1"/><path d="M1.5 6h13M1.5 10h13" stroke="#fff" stroke-width="1.1"/></svg>
        www.vitaridge.org
      </span>
    </div>
  </footer>
</main>
</body>
</html>
```